New design for www.TrimTable.com

On TrimTable you can find & book your hairdresser. TrimTable is the biggest platform in the Netherlands.

- The design should be a responcive design
- Should be able to go global, should fit in perfectly between all the big booking platforms like stayvo, ridlo etc,
- Should have te result of more bookings. :)
- We are ‘only’ asking a beautiful design, not a technical solution.
- We need a homepage (https://trimtable.com/), search resultpage ((https://trimtable.com/kapper/amsterdam/#), salonpage (https://trimtable.com/kapper/vorden/lumo-for-hair/), about us page (https://trimtable.com/aboutus/), for the hairdresser info page (https://trimtable.com/kapper/), login/register page (https://trimtable.com/account/signin/).

- On the page of the hairdresser there is a dynamic part. The part where you create your appointment. Please take a look at this part too after you choose your treatment (behandeling), employee (medewerker), Date (datum) and time (tijd). The part that you see after this, is the part where you fill in your data as a consumer.

I've added more logo's but mostly we use the green color.

A few of our competitors: www.plumsalo.com, www.korifex.com

Target Market(s)

All consumers

Industry/Entity Type

Hair And Beauty

Number of Pages Required

5+ page

Font styles to use
Sans Serif

Colors
abd036
c3c3c3
757575

Requirements
Must have
• Responsive
• We did an A/B test with the homepage. It turns out that option B works better then option A (take a look at the uploaded pictures). So what we need on the homepage: The USP's with the green checkboxes, The search button needs to by dynamic (changes for example from light green to dark green so you can see you can click it) The call to action sentence Zoek & Vind je kapsalon, the searchfield and searchbutton should be seperated.
Nice to have
• The style that we like is the flat design style. The website should be simple, clean and it should feel a bit like a luxury thing. Because an appointment with the hairdresser can be a real treat and luxury moment for yourself.
• The luxury feeling and flat design that is in the www.ridlo.com website is really nice for example. But then it has to be a bit more light and not so black and dark.

```html
<!DOCTYPE html>
<html lang="en">
<head>
<meta charset="utf-8">
<title>TrimTable – Hair Dresser Booking</title>
<link href="https://fonts.googleapis.com/css2?family=Oswald:wght@400;500;600&family=Open+Sans:wght@400;600;700&display=swap" rel="stylesheet">
<style>
  :root{
    --green:#8cc63f;
    --green-dark:#6fa52a;
    --orange:#f26522;
    --orange-dark:#d9531a;
    --ink:#333333;
    --grey:#757575;
    --grey-light:#c3c3c3;
    --panel:#f1f1f1;
    --dark:#2b2b2b;
    --white:#ffffff;
  }
  *{box-sizing:border-box;margin:0;padding:0}
  html,body{width:863px;height:1200px;overflow:hidden;background:var(--white)}
  body{font-family:'Open Sans',Arial,sans-serif;color:var(--ink)}
  .page{position:relative;width:863px;height:1200px;overflow:hidden}
  .heading{font-family:'Oswald','Arial Narrow',sans-serif;text-transform:uppercase}

  /* hero */
  .hero{position:absolute;left:0;top:0;width:863px;height:390px;
    background:radial-gradient(ellipse at 35% 45%,#b5553a 0%,#7a2a1c 35%,#3a1712 70%,#1e0e0c 100%)}
  .hero-shade{position:absolute;inset:0;background:linear-gradient(180deg,rgba(0,0,0,.05),rgba(0,0,0,.35))}
  .top-actions{position:absolute;top:10px;right:22px;display:flex;gap:6px}
  .top-actions .btn{height:24px;padding:0 10px;background:var(--green);color:var(--white);font-size:10px;font-weight:700;display:flex;align-items:center;border-radius:2px;text-transform:uppercase}
  .top-actions .menu{width:26px;padding:0;justify-content:center}
  .brand{position:absolute;top:108px;left:0;width:100%;display:flex;justify-content:center;align-items:center;gap:10px;color:var(--white);font-size:38px;font-weight:700;letter-spacing:-.5px}
  .brand .dot{width:34px;height:34px;border-radius:50%;background:var(--white)}
  .hero-title{position:absolute;top:186px;width:100%;text-align:center;color:var(--white);font-size:32px;font-weight:600;letter-spacing:.3px}
  .hero-sub{position:absolute;top:234px;width:100%;text-align:center;color:var(--white);font-size:13px;letter-spacing:.5px}
  .search{position:absolute;top:266px;left:262px;width:440px;height:32px;display:flex}
  .search input{flex:1;border:none;padding:0 12px;font-family:inherit;font-size:11px;color:var(--grey)}
  .search button{width:40px;border:none;background:var(--green);display:flex;align-items:center;justify-content:center}
  .appt-tab{position:absolute;top:340px;left:540px;width:296px;height:50px;background:rgba(30,30,30,.85);display:flex;align-items:center;gap:12px;padding-left:60px;color:var(--white);font-size:22px;font-weight:500}

  /* welcome */
  .welcome{position:absolute;left:70px;top:420px;width:450px}
  .welcome-head{display:flex;gap:12px;align-items:flex-start}
  .welcome-head h2{font-size:28px;line-height:30px;font-weight:500;color:var(--ink)}
  .welcome-head h2 span{color:var(--green)}
  .divider{position:absolute;left:230px;top:34px;width:220px;display:flex;align-items:center;gap:6px}
  .divider i{flex:1;height:1px;background:var(--ink)}
  .welcome p{margin-top:34px;font-size:10.5px;line-height:16px;color:var(--ink)}
  .cta{display:inline-block;margin-top:22px;background:var(--green);color:var(--white);font-size:13px;padding:7px 12px;letter-spacing:.5px}

  /* appointment form */
  .appt-form{position:absolute;left:540px;top:390px;width:296px;height:340px;background:var(--white);box-shadow:0 2px 8px rgba(0,0,0,.12);padding:16px 22px}
  .field{height:28px;border:1px solid #dcdcdc;margin-bottom:10px;display:flex;align-items:center;font-size:9.5px;color:var(--grey)}
  .field .ico{width:28px;height:100%;border-right:1px solid #dcdcdc;display:flex;align-items:center;justify-content:center;margin-right:8px}
  .field .caret{margin-left:auto;margin-right:10px}
  .submit{margin:14px auto 0;width:150px;height:30px;background:var(--orange);color:var(--white);font-size:16px;display:flex;align-items:center;justify-content:center;letter-spacing:.5px}

  /* services */
  .services{position:absolute;left:0;top:790px;width:863px;height:225px;background:var(--panel);display:flex;padding-top:40px}
  .service{flex:1;text-align:center}
  .service svg{display:block;margin:0 auto}
  .service h3{margin-top:14px;font-size:13px;font-weight:500;color:var(--ink)}

  /* footer */
  .footer{position:absolute;left:0;top:1015px;width:863px;height:160px;background:var(--orange);color:var(--white)}
  .col{position:absolute;top:16px}
  .col h4{font-size:12px;font-weight:500;margin-bottom:8px;letter-spacing:.4px}
  .col ul{list-style:none;font-size:9px;line-height:15px}
  .links li::before{content:"";display:inline-block;width:4px;height:4px;background:var(--white);margin-right:6px;vertical-align:middle}
  .contact li{display:flex;gap:6px;align-items:flex-start;margin-bottom:4px;max-width:150px}
  .gallery{display:grid;grid-template-columns:44px 44px;gap:4px}
  .gallery div{height:28px;background:linear-gradient(135deg,#6b4a3a,#2e211b)}
  .view-all{font-size:9px;line-height:12px;margin-top:5px;text-align:right;width:92px}
  .timings td{font-size:9px;padding:2px 8px 2px 0}
  .footer-brand{position:absolute;left:430px;top:124px;display:flex;align-items:center;gap:8px;font-size:22px;line-height:28px;font-weight:700}
  .footer-brand .dot{width:20px;height:20px;border-radius:50%;background:var(--white)}
  .phone{position:absolute;left:672px;top:940px;width:150px;height:235px;border-radius:22px;background:linear-gradient(160deg,#3a3a3a,#111);padding:30px 10px}
  .phone .screen{width:100%;height:170px;background:var(--green);display:flex;flex-direction:column;align-items:center;justify-content:center;gap:10px;color:var(--white)}
  .phone .screen b{font-size:16px}
  .phone .screen span{background:var(--green-dark);font-size:8px;padding:4px 8px;font-weight:700}
  .bottom-bar{position:absolute;left:0;top:1175px;width:863px;height:25px;background:var(--dark);color:#bdbdbd;font-size:8.5px;display:flex;align-items:center;padding:0 20px}
  .socials{margin-left:auto;display:flex;gap:5px}
  .socials i{width:14px;height:14px;border-radius:50%;border:1px solid #9a9a9a}
</style>
</head>
<body>
<div class="page">

  <header class="hero">
    <div role="img" aria-label="Portrait photo of a woman with long wavy copper hair" class="hero-shade"></div>
    <nav class="top-actions">
      <span class="btn menu"><svg width="12" height="10" viewBox="0 0 12 10"><path d="M0 1h12M0 5h12M0 9h12" stroke="#fff" stroke-width="2"/></svg></span>
      <span class="btn">Log in</span>
      <span class="btn">Register</span>
    </nav>
    <div class="brand"><span class="dot"></span>TrimTable</div>
    <h1 class="hero-title heading">The greatest hair dresser booking site</h1>
    <p class="hero-sub heading">We give you the look that matters</p>
    <form class="search">
      <input type="text" placeholder="Select salon, zip code">
      <button type="button" aria-label="Search"><svg width="16" height="16" viewBox="0 0 16 16"><circle cx="6.5" cy="6.5" r="5" fill="none" stroke="#fff" stroke-width="2"/><path d="M10.5 10.5L15 15" stroke="#fff" stroke-width="2"/></svg></button>
    </form>
    <div class="appt-tab heading">
      <svg width="22" height="22" viewBox="0 0 22 22"><rect x="2" y="4" width="18" height="16" fill="none" stroke="#fff" stroke-width="2"/><path d="M2 9h18M7 1v5M15 1v5" stroke="#fff" stroke-width="2"/></svg>
      Appointment Form
    </div>
  </header>

  <section class="welcome">
    <div class="welcome-head">
      <svg width="30" height="40" viewBox="0 0 30 40"><path d="M15 0C7 0 0 6.5 0 15c0 11 15 25 15 25s15-14 15-25C30 6.5 23 0 15 0z" fill="var(--green)"/><circle cx="15" cy="14" r="6" fill="#fff"/></svg>
      <h2 class="heading">Welcome to<br><span>TrimTable</span></h2>
    </div>
    <div class="divider"><i></i>
      <svg width="24" height="18" viewBox="0 0 24 18"><circle cx="4" cy="4" r="3" fill="none" stroke="#333" stroke-width="1.5"/><circle cx="4" cy="14" r="3" fill="none" stroke="#333" stroke-width="1.5"/><path d="M6.5 5.5L23 15M6.5 12.5L23 3" stroke="#333" stroke-width="1.5"/></svg>
    </div>
    <p>Lorem ipsum dolor sit amet, consectetuer adipiscing elit, sed diam nonummy nibh euismod tincidunt ut laoreet dolore magna aliquam erat volutpat. Ut wisi enim ad minim veniam, quis nostrud exerci tation ullamcorper suscipit lobortis nisl ut aliquip ex ea commodo consequat. Duis autem vel eum iriure dolor in hendrerit in vulputate velit esse molestie consequat, vel illum dolore eu feugiat nulla facilisis at vero eros et accumsan et iusto odio dignissim qui blandit praesent luptatum zzril delenit augue duis dolore.</p>
    <span class="cta heading">Get started</span>
  </section>

  <form class="appt-form">
    <div class="field"><span class="ico"><svg width="10" height="10"><rect x="1" y="2" width="8" height="7" fill="none" stroke="#999"/></svg></span>Appointment date</div>
    <div class="field"><span class="ico"><svg width="10" height="10"><circle cx="5" cy="5" r="4" fill="none" stroke="#999"/><path d="M5 2v3h2" stroke="#999" fill="none"/></svg></span>Appointment time</div>
    <div class="field"><span class="ico"><svg width="10" height="10"><circle cx="5" cy="3" r="2.2" fill="none" stroke="#999"/><path d="M1 10c0-3 8-3 8 0" stroke="#999" fill="none"/></svg></span>Name</div>
    <div class="field"><span class="ico"><svg width="10" height="10"><rect x="2.5" y="0.5" width="5" height="9" rx="1" fill="none" stroke="#999"/></svg></span>Phone Number</div>
    <div class="field"><span class="ico"><svg width="10" height="10"><rect x="0.5" y="2" width="9" height="6" fill="none" stroke="#999"/><path d="M0.5 2l4.5 3.5L9.5 2" stroke="#999" fill="none"/></svg></span>Email</div>
    <div class="field"><span class="ico"><svg width="10" height="10"><circle cx="5" cy="5" r="4" fill="none" stroke="#999"/></svg></span>Gender<span class="caret"><svg width="8" height="5"><path d="M0 0l4 5 4-5z" fill="#999"/></svg></span></div>
    <div class="submit heading">Submit</div>
  </form>

  <section class="services">
    <div class="service">
      <svg width="56" height="56" viewBox="0 0 56 56"><circle cx="14" cy="42" r="7" fill="none" stroke="var(--orange)" stroke-width="4"/><circle cx="42" cy="42" r="7" fill="none" stroke="var(--orange)" stroke-width="4"/><path d="M18 36L44 6M38 36L12 6" stroke="var(--orange)" stroke-width="4"/></svg>
      <h3 class="heading">Cutting and styling</h3>
    </div>
    <div class="service">
      <svg width="56" height="56" viewBox="0 0 56 56"><rect x="22" y="4" width="12" height="26" rx="3" fill="var(--orange)"/><path d="M18 30h20l-4 22H22z" fill="var(--orange)"/></svg>
      <h3 class="heading">Hair color</h3>
    </div>
    <div class="service">
      <svg width="56" height="56" viewBox="0 0 56 56"><rect x="10" y="22" width="36" height="30" rx="6" fill="var(--orange)"/><rect x="20" y="8" width="16" height="14" fill="var(--orange)"/><circle cx="28" cy="37" r="6" fill="#fff"/></svg>
      <h3 class="heading">Hair treatment</h3>
    </div>
    <div class="service">
      <svg width="56" height="56" viewBox="0 0 56 56"><rect x="6" y="22" width="44" height="10" rx="3" fill="var(--orange)"/><path d="M10 32h36v6H10z" fill="var(--orange)" opacity=".6"/><rect x="24" y="8" width="8" height="14" fill="var(--orange)"/></svg>
      <h3 class="heading">Beard treatment</h3>
    </div>
    <div class="service">
      <svg width="56" height="56" viewBox="0 0 56 56"><circle cx="28" cy="28" r="24" fill="var(--orange)"/><path d="M17 29l8 8 15-17" stroke="#fff" stroke-width="5" fill="none"/></svg>
      <h3 class="heading">The finish</h3>
    </div>
  </section>

  <footer class="footer">
    <div class="col" style="left:50px">
      <h4 class="heading">Quick links</h4>
      <ul class="links"><li>Home</li><li>About Us</li><li>Salon</li><li>Search</li><li>Contact</li><li>Login</li></ul>
    </div>
    <div class="col contact" style="left:170px">
      <h4 class="heading">Contact details</h4>
      <ul>
        <li><svg width="9" height="11"><path d="M4.5 0C2 0 0 2 0 4.5 0 8 4.5 11 4.5 11S9 8 9 4.5C9 2 7 0 4.5 0z" fill="#fff"/></svg>Keizersgracht 48, 1015 Amsterdam, Netherlands</li>
        <li><svg width="9" height="11"><rect x="1.5" y="0.5" width="6" height="10" rx="1" fill="#fff"/></svg>+31 20 555 0142</li>
        <li><svg width="9" height="11"><rect x="0" y="2" width="9" height="7" fill="#fff"/></svg>info@trimtable.com</li>
      </ul>
    </div>
    <div class="col" style="left:360px">
      <h4 class="heading">Our gallery</h4>
      <div class="gallery" role="img" aria-label="Salon photo thumbnails"><div></div><div></div><div></div><div></div></div>
      <p class="view-all heading">View all</p>
    </div>
    <div class="col" style="left:495px">
      <h4 class="heading">Office timings</h4>
      <table class="timings">
        <tr><td>MON - THU</td><td>9:00 AM - 7:30 PM</td></tr>
        <tr><td>FRI &amp; SAT</td><td>9:00 AM - 8:30 PM</td></tr>
        <tr><td>SUN</td><td>CLOSED</td></tr>
      </table>
    </div>
    <div class="footer-brand"><span class="dot"></span>TrimTable</div>
  </footer>

  <div class="phone" role="img" aria-label="Smartphone showing the TrimTable app">
    <div class="screen"><b>TrimTable</b><span>DOWNLOAD APP</span></div>
  </div>

  <div class="bottom-bar">
    <span>Copyright 2015 TrimTable | All Rights Reserved</span>
    <div class="socials"><i></i><i></i><i></i><i></i></div>
  </div>

</div>
</body>
</html>
```